Upmarket Dessert Lounge needs a Business Card Design

We are an upmarket dessert lounge needing a business card to match our image.

We want something that is simple yet beautiful, feminine, classy, sophisticated and elegant. We want it to stand out and don't mind if it is bold.

The design should include our logo and colours of red or maroon with gold highlights. We don't mind if black is used.

Marlow & Quince

Target Market(s)

For those who like to indulge or treat themselves and give in to their temptations on good quality desserts.

Industry/Entity Type

Business

Requirements
Must have
• Must include our logo and our name

Marlow & Quince

M & Q

```html
<!DOCTYPE html>
<html lang="en">
<head>
<meta charset="utf-8">
<title>Marlow &amp; Quince — Business Card</title>
<link rel="stylesheet" href="https://fonts.googleapis.com/css2?family=EB+Garamond:ital,wght@0,400;0,600;0,700;1,400&display=swap">
<style>
  :root {
    --backdrop: #3a3a3a;
    --card: #fdd59c;
    --card-pattern-light: #fddcaa;
    --card-pattern-deep: #f8c98a;
    --maroon: #8b1a1f;
  }
  * { box-sizing: border-box; margin: 0; padding: 0; }
  html, body {
    width: 1200px;
    height: 900px;
    overflow: hidden;
    background: var(--backdrop);
    font-family: "EB Garamond", "Times New Roman", serif;
    color: var(--maroon);
  }
  .stage { position: relative; width: 1200px; height: 900px; }
  .card {
    position: absolute;
    top: 308px;
    width: 513px;
    height: 283px;
    border-radius: 24px;
    background: var(--card);
    overflow: hidden;
  }
  .card--front { left: 73px; }
  .card--back { left: 615px; }
  .card__pattern {
    position: absolute;
    inset: 0;
    background: radial-gradient(ellipse at 50% 50%, var(--card-pattern-light) 0%, var(--card) 55%, var(--card-pattern-deep) 100%);
    opacity: 0.9;
  }
  .brand-name {
    position: absolute;
    left: 0; right: 0;
    top: 118px;
    text-align: center;
    font-size: 36px;
    font-weight: 400;
    letter-spacing: 1px;
    line-height: 1.2;
    white-space: nowrap;
  }
  .tagline {
    position: absolute;
    left: 0; right: 0;
    top: 238px;
    text-align: center;
    font-size: 11.5px;
    font-weight: 700;
    letter-spacing: 6.6px;
    white-space: nowrap;
  }
  .owner {
    position: absolute;
    left: 0; right: 0;
    top: 25px;
    text-align: center;
    font-size: 15px;
    white-space: nowrap;
  }
  .owner__name { font-weight: 700; }
  .owner__role { font-style: italic; }
  .monogram {
    position: absolute;
    left: 0; right: 0;
    top: 100px;
    text-align: center;
    font-size: 70px;
    font-weight: 400;
    line-height: 1;
  }
  .contact {
    position: absolute;
    top: 228px;
    left: 0; right: 0;
    display: flex;
    justify-content: center;
    gap: 16px;
    font-size: 14px;
    line-height: 16px;
    white-space: nowrap;
  }
  .contact__place { text-align: right; }
  .contact__online { text-align: left; }
</style>
</head>
<body>
<main class="stage">
  <section class="card card--front">
    <div class="card__pattern" role="img" aria-label="Soft tonal flourish pattern across the card"></div>
    <div class="brand-name">MARLOW &amp; QUINCE</div>
    <div class="tagline">UPMARKET DESSERT LOUNGE</div>
  </section>

  <section class="card card--back">
    <div class="card__pattern" role="img" aria-label="Soft tonal flourish pattern across the card"></div>
    <div class="owner"><span class="owner__name">CLARA WHITBY</span> <span class="owner__role">— founder and owner</span></div>
    <div class="monogram">M&amp;Q</div>
    <div class="contact">
      <div class="contact__place">Hobart, Tasmania<br>555 555 55 55</div>
      <div class="contact__online">info@marlow-quince.com | www.marlow-quince.com<br>www.quincelounge.net/marlow</div>
    </div>
  </section>
</main>
</body>
</html>
```